Business Card and Presentation Folder for Roofing Company
marla
Business Card and Presentation Folder for Roofing Company - Construction
Creative Brief
Professional
Pete Vance
Field Supervisor
27815 Larkspur Ave Suite 311 Kirkwood, MO 63122
866-517-TILE
pvance@gablecrest.example
www.GableCrestRenewal.example
IL License #287.443512
stay with our colors of Yellow PMS 106, Black, and White
we want Logo Residential & Commercial 314-926-1758 Accredited Member of the QTC with an A+ Rating possible tag line: Every need met beneath a sturdy Crest! or: Dedicated to being the most Trusted name in the Roofing Industry!
MarlaShingleCo MarlaShingleCo
COMBINE #217 AND #208 AND I WILL FINALIZE
#216...PLEASE MAKE THE CHANGES I REQUESTED SO I CAN FINALIZE THIS......
I extended the context
I uploaded an example of what I want our 2 presentation folders to look like: commercial folder: the 9 ICONS WILL BE: Flat roof Industrial building, Factory, City Highrise building, Apartment (3 story), Church, Gas Station, Restaurant, Hotel, & Bank Residential Folder: 9 ICONS WILL BE: House, House with flat roof, Condo, Siding, Gutters, Insulation, Ventilation, Storm Damage, Water&Fire Damage (together)
I uploaded our logos. Our colors are Yellow PMS106, Black, and White.....please use only these colors. Need business cards and Presentation Folder 9x12" (standard size) I will need the final files in Photoshop PSD file with all layers visible so I can make any future changes myself. Thanks Marla

```html
<!DOCTYPE html>
<html lang="en">
<head>
<meta charset="utf-8">
<title>Gable Crest Renewal – Business Card and Presentation Folder</title>
<link href="https://fonts.googleapis.com/css2?family=Oswald:wght@600&family=Tinos:ital,wght@0,400;1,400&display=swap" rel="stylesheet">
<style>
  :root {
    --yellow: #f5e31a;
    --black: #111111;
    --white: #ffffff;
    --stage-top: #cfcfcf;
    --stage-bottom: #d9d9d9;
    --paper-shade: #efefef;
    --brand-font: "Oswald", "Arial Narrow", sans-serif;
    --text-font: "Tinos", "Times New Roman", serif;
  }
  * { box-sizing: border-box; margin: 0; padding: 0; }
  html, body { width: 1200px; height: 1049px; overflow: hidden; }
  body { position: relative; background: var(--stage-bottom); font-family: var(--text-font); }

  .cards-area { position: absolute; left: 0; top: 0; width: 1200px; height: 292px; background: var(--stage-top); }
  .folder-area { position: absolute; left: 0; top: 300px; width: 1200px; height: 749px; background: var(--stage-bottom); }

  .card {
    position: absolute; top: 22px; width: 450px; height: 252px;
    background: var(--black); border-radius: 16px; overflow: hidden; color: var(--white);
  }
  .card--front { left: 136px; }
  .card--back { left: 612px; }

  /* front */
  .holder { position: absolute; left: 26px; top: 104px; }
  .holder-name { font-size: 32px; color: var(--yellow); line-height: 1; }
  .holder-title { font-size: 17px; margin-top: 6px; }
  .contact-list { position: absolute; left: 224px; top: 24px; list-style: none; }
  .contact-list li { display: flex; align-items: center; font-size: 11.5px; line-height: 1; height: 21px; white-space: nowrap; }
  .contact-list .icon { width: 12px; height: 12px; margin-right: 8px; flex: none; }
  .contact-list .continued { padding-left: 20px; }
  .front-band { position: absolute; left: 0; bottom: 0; width: 100%; height: 34px; display: flex; }
  .license { flex: 1; background: var(--yellow); color: var(--black); font-size: 12px; display: flex; align-items: center; padding-left: 26px; }
  .band-mark { width: 116px; background: var(--black); display: flex; align-items: center; justify-content: center; }

  /* brand name set as text */
  .brand-name { font-family: var(--brand-font); font-weight: 600; color: var(--yellow); text-transform: uppercase; text-align: center; line-height: 0.95; }
  .brand-name--small { font-size: 20px; letter-spacing: 1px; }
  .brand-name span { display: block; }

  /* back */
  .back-brand { position: absolute; left: 0; right: 0; top: 24px; }
  .back-brand .initials { font-size: 62px; letter-spacing: 4px; }
  .back-brand .words { font-size: 27px; letter-spacing: 1px; }
  .back-band { position: absolute; left: 0; top: 170px; width: 100%; height: 44px; background: var(--yellow); color: var(--black); text-align: center; font-size: 13px; line-height: 1.35; padding-top: 4px; }
  .back-tagline { position: absolute; left: 0; right: 0; bottom: 10px; text-align: center; font-size: 11px; font-style: italic; color: var(--yellow); }

  /* folder */
  .folder-cover { position: absolute; left: 40px; top: 48px; width: 390px; height: 640px; background: var(--black); box-shadow: 0 6px 18px rgba(0,0,0,.25); }
  .cover-brand { position: absolute; left: 0; right: 0; top: 120px; }
  .cover-brand .initials { font-size: 96px; letter-spacing: 6px; }
  .cover-brand .words { font-size: 40px; letter-spacing: 2px; }
  .cover-stripe { position: absolute; left: 0; right: 0; bottom: 40px; height: 8px; background: var(--yellow); }
  .cover-mark { position: absolute; right: 18px; bottom: 12px; }
  .cover-mark .brand-name { font-size: 16px; letter-spacing: 1px; }

  .folder-inside { position: absolute; left: 470px; top: 48px; width: 690px; height: 640px; display: flex; box-shadow: 0 6px 18px rgba(0,0,0,.25); }
  .inside-panel { width: 345px; height: 100%; background: var(--white); position: relative; }
  .inside-panel--left { background: linear-gradient(90deg, var(--white) 70%, var(--paper-shade)); }
  .pocket { position: absolute; left: 0; bottom: 0; width: 345px; height: 210px; }
</style>
</head>
<body>
  <section class="cards-area">
    <article class="card card--front">
      <div class="holder">
        <p class="holder-name">Pete Vance</p>
        <p class="holder-title">Field Supervisor</p>
      </div>
      <ul class="contact-list">
        <li><svg class="icon" viewBox="0 0 12 12"><circle cx="6" cy="6" r="6" fill="#f5e31a"/></svg>866-517-TILE (Toll Free)</li>
        <li><svg class="icon" viewBox="0 0 12 12"><circle cx="6" cy="6" r="6" fill="#f5e31a"/></svg>314-926-1758</li>
        <li><svg class="icon" viewBox="0 0 12 12"><circle cx="6" cy="6" r="6" fill="#f5e31a"/></svg>314-555-0142</li>
        <li><svg class="icon" viewBox="0 0 12 12"><circle cx="6" cy="6" r="6" fill="#f5e31a"/></svg>866-555-0187</li>
        <li><svg class="icon" viewBox="0 0 12 12"><circle cx="6" cy="6" r="6" fill="#f5e31a"/></svg>pvance@gablecrest.example</li>
        <li><svg class="icon" viewBox="0 0 12 12"><circle cx="6" cy="6" r="6" fill="#f5e31a"/></svg>www.GableCrestRenewal.example</li>
        <li><svg class="icon" viewBox="0 0 12 12"><circle cx="6" cy="6" r="6" fill="#f5e31a"/></svg>27815 Larkspur Ave Suite 311</li>
        <li class="continued">Fenwick Hills, MO 64190</li>
      </ul>
      <div class="front-band">
        <p class="license">IL License #287.443512</p>
        <div class="band-mark"><p class="brand-name brand-name--small">GCR</p></div>
      </div>
    </article>

    <article class="card card--back">
      <div class="back-brand brand-name">
        <span class="initials">GCR</span>
        <span class="words">Gable Crest</span>
        <span class="words">Renewal</span>
      </div>
      <div class="back-band">
        <p>Residential &amp; Commercial : 314-926-1758</p>
        <p>Accredited Member of the QTC with an A+ Rating</p>
      </div>
      <p class="back-tagline">Dedicated to being the most Trusted name in the Roofing Industry!</p>
    </article>
  </section>

  <section class="folder-area">
    <article class="folder-cover">
      <div class="cover-brand brand-name">
        <span class="initials">GCR</span>
        <span class="words">Gable Crest</span>
        <span class="words">Renewal</span>
      </div>
      <div class="cover-stripe"></div>
      <div class="cover-mark"><p class="brand-name">GCR</p></div>
    </article>

    <article class="folder-inside">
      <div class="inside-panel inside-panel--left"></div>
      <div class="inside-panel inside-panel--right">
        <svg class="pocket" viewBox="0 0 345 210" preserveAspectRatio="none">
          <polygon points="0,40 120,40 150,0 345,0 345,210 0,210" fill="#111111"/>
        </svg>
      </div>
    </article>
  </section>
</body>
</html>
```